Speisekarten-Design für gehobenes italienisches Restaurant
Zielgruppe
Wir sind ein gehobenes italienisches Restaurant und suchen ein neues Design für unsere Speisekarte. Wir haben ein eher älteres Publikum.
Aufgabenstellung
Wir möchten eine elegantes modernes Design. Einzelseiten im A4 Format.

```html
<!DOCTYPE html>
<html lang="de">
<head>
<meta charset="utf-8">
<title>Casa del Faro – Speisekarte</title>
<link rel="stylesheet" href="https://fonts.googleapis.com/css2?family=Great+Vibes&family=Crimson+Text:wght@400;600&family=Cormorant+Garamond:ital,wght@1,700&family=Open+Sans:wght@400;600&display=swap">
<style>
:root{
  --bg:#ece9e4;
  --paper:#d9d1c5;
  --ink:#1e1b18;
  --muted:#3a342e;
  --maroon:#7a1a2a;
  --olive:#3b3a32;
  --green:#1f9a3a;
  --white:#ffffff;
  --red:#e3141b;
  --soup:#c9542a;
  --caprese:#c8443a;
}
*{margin:0;padding:0;box-sizing:border-box}
html,body{width:1200px;height:675px;overflow:hidden;background:var(--bg)}
body{position:relative;font-family:"Open Sans",sans-serif;color:var(--ink)}
.page{position:absolute;top:141px;width:279px;height:393px;background:var(--paper);box-shadow:0 2px 6px rgba(0,0,0,.25)}
.page--cover-food{left:12px}
.page--food{left:313px}
.page--cover-drinks{left:614px}
.page--drinks{left:912px}
.ornament{position:absolute;top:22px;width:72px;height:24px;background:linear-gradient(90deg,rgba(59,58,50,.15),rgba(59,58,50,.55),rgba(59,58,50,.15));border-radius:12px}
.ornament--left{left:7px}
.ornament--right{right:7px}
.brand{position:absolute;top:27px;left:0;width:100%;text-align:center;font-family:"Crimson Text",serif;font-weight:600;font-size:15px;color:var(--maroon);line-height:16px}
.brand::before{content:"";display:inline-block;width:7px;height:7px;border-radius:50%;background:var(--maroon);margin-right:5px;vertical-align:1px}
.cover-title{position:absolute;top:160px;left:0;width:100%;text-align:center;font-family:"Great Vibes",cursive;font-size:48px;text-shadow:2px 3px 3px rgba(0,0,0,.25)}
.footer{position:absolute;top:355px;left:0;width:100%;text-align:center;font-family:"Crimson Text",serif;font-size:6.3px;line-height:8.6px}
.flag{position:absolute;top:381px;left:49px;width:181px;height:5px;display:flex}
.flag span{flex:1}
.flag .g{background:var(--green)}.flag .w{background:var(--white)}.flag .r{background:var(--red)}
.section-title{position:absolute;font-family:"Cormorant Garamond",serif;font-style:italic;font-weight:700;font-size:13px;text-shadow:1px 1px 1px rgba(0,0,0,.2)}
.photo{position:absolute;border-radius:50%}
.photo--soup{left:62px;top:62px;width:44px;height:33px;background:radial-gradient(circle at 50% 45%,#e06a34,#8a2c16)}
.photo--caprese{left:146px;top:196px;width:49px;height:25px;background:radial-gradient(circle at 50% 50%,#f1ece6,#c8443a 70%,#7d8a5a)}
.dish{position:absolute;width:118px}
.dish__name{font-size:6.6px;line-height:8px}
.dish__name sup,.drink sup{font-size:3.4px}
.dish__desc{font-size:4.2px;line-height:5.1px;font-weight:600;width:88px}
.dish__price{position:absolute;top:8px;font-size:4.4px;font-weight:600}
.voucher{position:absolute;left:128px;top:85px;width:139px;height:70px;border:1px solid #8a8278;background:#e2dbd1}
.voucher__kicker{text-align:center;font-family:"Crimson Text",serif;font-style:italic;font-weight:600;font-size:5.6px;margin-top:1px}
.voucher__title{text-align:center;font-family:"Great Vibes",cursive;font-size:15px;line-height:16px}
.voucher__text{font-size:4.9px;line-height:6.3px;padding:4px 3px 0}
.script-head{position:absolute;font-family:"Great Vibes",cursive;font-size:12px}
.size{position:absolute;font-size:3.6px}
.drink{position:absolute;font-size:6.4px;line-height:8px;white-space:nowrap}
.price{position:absolute;font-size:6.4px;font-weight:600;line-height:8px}
</style>
</head>
<body>

<!-- Cover: Speisen -->
<section class="page page--cover-food">
  <div class="ornament ornament--left" role="img" aria-label="Olivenzweig-Ornament"></div>
  <div class="brand">Casa del Faro</div>
  <div class="ornament ornament--right" role="img" aria-label="Olivenzweig-Ornament"></div>
  <h1 class="cover-title">Speisen</h1>
  <div class="footer">Ristorante-Pizzeria Casa-del-Faro<br>Lindenallee 14, 61234 Talheim-Auental<br>Tel: 04521 - 55 210 90</div>
  <div class="flag"><span class="g"></span><span class="w"></span><span class="r"></span></div>
</section>

<!-- Speisen: Suppen & Antipasti -->
<section class="page page--food">
  <div class="ornament ornament--left" role="img" aria-label="Olivenzweig-Ornament"></div>
  <div class="brand">Casa del Faro</div>
  <div class="ornament ornament--right" role="img" aria-label="Olivenzweig-Ornament"></div>

  <h2 class="section-title" style="left:16px;top:66px">Suppen</h2>
  <div class="photo photo--soup" role="img" aria-label="Foto einer Tomatensuppe in einer Schale"></div>

  <div class="dish" style="left:13px;top:96px"><div class="dish__name">Tomatensuppe <sup>G</sup></div><div class="dish__desc">Mit Sahnehäubchen aufwartend</div><span class="dish__price" style="left:96px">6.60</span></div>
  <div class="dish" style="left:13px;top:114px"><div class="dish__name">Minestrone</div><div class="dish__desc">Mit frischem Gemüse</div><span class="dish__price" style="left:96px">6.90</span></div>
  <div class="dish" style="left:13px;top:133px"><div class="dish__name">Tortellini in Brodo <sup>L</sup></div><div class="dish__desc">Hackfleisch gefüllte Tortellini<br>in kräftiger Brühe</div><span class="dish__price" style="left:96px">6.90</span></div>
  <div class="dish" style="left:13px;top:157px"><div class="dish__name">Italienische Zwiebelsuppe <sup>G</sup></div><div class="dish__desc">Die feine hausgemachte Suppe erreicht Sie frisch aus dem Ofen mit einer knusprigen Pizzateighaube</div><span class="dish__price" style="left:96px">9.50</span></div>

  <div class="voucher">
    <div class="voucher__kicker">Genuss verschenken</div>
    <div class="voucher__title">Gutschein</div>
    <p class="voucher__text">Verschenken Sie Genuss!<br>Im Ristorante Casa del Faro stellen wir Ihnen<br>gern einen Geschenkgutschein aus,<br>der den bedachten Lieben die Welt der<br>mediterran-italienischen Küche zu Füßen legt.</p>
  </div>

  <h2 class="section-title" style="left:84px;top:203px">Antipasti</h2>
  <div class="photo photo--caprese" role="img" aria-label="Foto eines Caprese-Tellers mit Tomate und Mozzarella"></div>

  <div class="dish" style="left:13px;top:231px"><div class="dish__name">Gebackener Schafskäse mit Salat <sup>G</sup></div><div class="dish__desc">Panierter und frittierter Schafskäse<br>an Salatbouquet</div><span class="dish__price" style="left:105px">13.90</span></div>
  <div class="dish" style="left:13px;top:256px"><div class="dish__name">Carpaccio di Manzo <sup>G,L</sup></div><div class="dish__desc">Hauchfein geschnittene Rinderfilet-Scheiben auf Rucolabett. Mit frischen Champignons, Parmesankäse &amp; Sellerie</div><span class="dish__price" style="left:105px">15.90</span></div>
  <div class="dish" style="left:13px;top:287px"><div class="dish__name">Garnelen-Pfännchen <sup>B</sup></div><div class="dish__desc">Leckere gebratene Garnelen in mit Knoblauch und Kräutern abgeschmeckter Soße</div><span class="dish__price" style="left:105px">16.90</span></div>
  <div class="dish" style="left:13px;top:311px"><div class="dish__name">Vitello Tonnato <sup>E,D,G</sup></div><div class="dish__desc">Fein geschnittener Kalbsbraten bedeckt mit Thunfischcreme, angemacht mit Oliven, Kapern &amp; Sardellen</div><span class="dish__price" style="left:105px">14.50</span></div>

  <div class="dish" style="left:164px;top:231px"><div class="dish__name">Insalata di Mare <sup>B,D,R</sup></div><div class="dish__desc">Hausgemachter Meeresfrüchte-Salat erwartet Sie hier.<br>Dazu reichen wir Ihnen Brot</div><span class="dish__price" style="left:94px">15.90</span></div>
  <div class="dish" style="left:164px;top:261px"><div class="dish__name">Anitpasto Misto <sup>E,B,D,G,R</sup></div><div class="dish__desc">Genießen Sie eine von unserem Küchenchef zusammengestellte leckere Kombination kalt-warmer Vorspeisen-Spezialitäten aus mediterranen Gefilden</div><span class="dish__price" style="left:94px">15.90</span></div>
  <div class="dish" style="left:164px;top:295px"><div class="dish__name">Caprese <sup>G</sup></div><div class="dish__desc">Italienische Vorspeisen-Spezialität u.a. aus Tomatenscheiben, Mozzarella-Käse und Basilikum</div><span class="dish__price" style="left:94px">9.90</span></div>

  <div class="footer">Ristorante-Pizzeria Casa-del-Faro<br>Lindenallee 14, 61234 Talheim-Auental<br>Tel: 04521 - 55 210 90</div>
  <div class="flag"><span class="g"></span><span class="w"></span><span class="r"></span></div>
</section>

<!-- Cover: Getränke -->
<section class="page page--cover-drinks">
  <div class="ornament ornament--left" role="img" aria-label="Olivenzweig-Ornament"></div>
  <div class="brand">Casa del Faro</div>
  <div class="ornament ornament--right" role="img" aria-label="Olivenzweig-Ornament"></div>
  <h1 class="cover-title">Getränke</h1>
  <div class="footer">Ristorante-Pizzeria Casa-del-Faro<br>Lindenallee 14, 61234 Talheim-Auental<br>Tel: 04521 - 55 210 90</div>
  <div class="flag"><span class="g"></span><span class="w"></span><span class="r"></span></div>
</section>

<!-- Getränke -->
<section class="page page--drinks">
  <div class="ornament ornament--left" role="img" aria-label="Olivenzweig-Ornament"></div>
  <div class="brand">Casa del Faro</div>
  <div class="ornament ornament--right" role="img" aria-label="Olivenzweig-Ornament"></div>

  <h2 class="script-head" style="left:9px;top:68px">Alkoholfrei</h2>
  <span class="size" style="left:98px;top:88px">0,2l</span><span class="size" style="left:130px;top:88px">0,4l</span>
  <span class="drink" style="left:9px;top:98px">Cola <sup>1,9,17</sup></span><span class="price" style="left:92px;top:98px">2.90</span><span class="price" style="left:124px;top:98px">4.70</span>
  <span class="drink" style="left:9px;top:110px">Cola light <sup>1,9,11,12</sup></span><span class="price" style="left:92px;top:110px">2.90</span><span class="price" style="left:124px;top:110px">4.70</span>
  <span class="drink" style="left:9px;top:123px">Orangenlimonade <sup>1,G</sup></span><span class="price" style="left:92px;top:123px">2.90</span><span class="price" style="left:124px;top:123px">4.70</span>
  <span class="drink" style="left:9px;top:135px">Zitronenlimonade</span><span class="price" style="left:92px;top:135px">2.90</span><span class="price" style="left:124px;top:135px">4.70</span>
  <span class="drink" style="left:9px;top:147px">Cola-Mix <sup>1,9,17,G</sup></span><span class="price" style="left:92px;top:147px">2.90</span><span class="price" style="left:124px;top:147px">4.70</span>

  <h2 class="script-head" style="left:12px;top:160px">Fruchtig</h2>
  <span class="size" style="left:98px;top:176px">0,2l</span><span class="size" style="left:130px;top:176px">0,4l</span>
  <span class="drink" style="left:9px;top:187px">Apfelsaft</span><span class="price" style="left:92px;top:187px">2.90</span><span class="price" style="left:124px;top:187px">4.70</span>
  <span class="drink" style="left:9px;top:199px">Apfelsaft-Schorle</span><span class="price" style="left:92px;top:199px">2.90</span><span class="price" style="left:124px;top:199px">4.70</span>
  <span class="drink" style="left:9px;top:211px">Orangensaft</span><span class="price" style="left:92px;top:211px">2.90</span><span class="price" style="left:124px;top:211px">4.70</span>
  <span class="drink" style="left:9px;top:223px">Kirschnektar</span><span class="price" style="left:92px;top:223px">2.90</span><span class="price" style="left:124px;top:223px">4.70</span>
  <span class="drink" style="left:9px;top:236px">Orangensaft</span><span class="price" style="left:92px;top:236px">2.90</span><span class="price" style="left:124px;top:236px">4.70</span>
  <span class="drink" style="left:9px;top:248px">Kirschnektar</span><span class="price" style="left:92px;top:248px">2.90</span><span class="price" style="left:124px;top:248px">4.70</span>
  <span class="drink" style="left:9px;top:260px">Kirschnektar</span><span class="price" style="left:92px;top:260px">2.90</span><span class="price" style="left:124px;top:260px">4.70</span>

  <h2 class="script-head" style="left:9px;top:279px">Eistee</h2>
  <span class="size" style="left:129px;top:305px">0,33l</span>
  <span class="drink" style="left:9px;top:304px">Eistee della Casa</span>
  <span class="drink" style="left:13px;top:316px">Pfirsich</span><span class="price" style="left:124px;top:316px">5.20</span>
  <span class="drink" style="left:13px;top:328px">Zitrone</span><span class="price" style="left:124px;top:328px">5.20</span>

  <h2 class="script-head" style="left:154px;top:68px">Wasser</h2>
  <span class="size" style="left:223px;top:88px">0,25l</span><span class="size" style="left:257px;top:88px">0,75l</span>
  <span class="drink" style="left:154px;top:98px">Acqua Frizzante</span><span class="price" style="left:220px;top:98px">2.80</span><span class="price" style="left:254px;top:98px">6.50</span>
  <span class="drink" style="left:154px;top:110px">Acqua Fonte Still</span><span class="price" style="left:220px;top:110px">2.90</span><span class="price" style="left:254px;top:110px">6.90</span>
  <span class="drink" style="left:154px;top:123px">Acqua Fonte</span><span class="price" style="left:220px;top:123px">2.90</span><span class="price" style="left:254px;top:123px">6.90</span>

  <h2 class="script-head" style="left:154px;top:157px">Erfrischend</h2>
  <span class="size" style="left:226px;top:176px">0,2l</span><span class="size" style="left:259px;top:176px">0,4l</span>
  <span class="drink" style="left:154px;top:187px">Bitter Lemon <sup>3,10</sup></span><span class="price" style="left:220px;top:187px">3.20</span><span class="price" style="left:254px;top:187px">5.10</span>
  <span class="drink" style="left:154px;top:200px">Ginger Ale <sup>1</sup></span><span class="price" style="left:220px;top:200px">3.20</span><span class="price" style="left:254px;top:200px">5.10</span>
  <span class="drink" style="left:154px;top:212px">Tonic Water <sup>10</sup></span><span class="price" style="left:220px;top:212px">3.30</span><span class="price" style="left:254px;top:212px">5.30</span>

  <span class="size" style="left:226px;top:263px">0,2l</span>
  <span class="drink" style="left:154px;top:273px">H-Milch</span><span class="price" style="left:220px;top:273px">2.20</span>

  <div class="footer">Ristorante-Pizzeria Casa-del-Faro<br>Lindenallee 14, 61234 Talheim-Auental<br>Tel: 04521 - 55 210 90</div>
  <div class="flag"><span class="g"></span><span class="w"></span><span class="r"></span></div>
</section>

</body>
</html>
```